Letterhead, stationery and email signature for construction business

I need the letterhead, stationery and email signature designs for a construction business. I want them to have a corporate feel to them.

I've attached the logo for reference.

```html
<!DOCTYPE html>
<html lang="en">
<head>
<meta charset="utf-8">
<title>Stonevale Works – Stationery Set</title>
<link href="https://fonts.googleapis.com/css2?family=Montserrat:wght@500;600;700&family=Lato:wght@400;700&family=Parisienne&display=swap" rel="stylesheet">
<style>
:root{
  --blue:#2a5ea8;
  --blue-deep:#254f97;
  --curve:#5a5f6b;
  --paper:#ffffff;
  --ink:#2b2b2b;
  --bg:#e8e9eb;
}
*{margin:0;padding:0;box-sizing:border-box}
html,body{width:1200px;height:889px;overflow:hidden;background:var(--bg)}
body{position:relative;font-family:'Lato',sans-serif;color:var(--ink)}
.piece{position:absolute;background:var(--paper);overflow:hidden}
.band{position:absolute;left:0;bottom:0;width:100%}
.brand{display:flex;align-items:center;gap:4px;font-family:'Montserrat',sans-serif;font-weight:700;color:var(--blue);white-space:nowrap;letter-spacing:.02em}
.brand .mark{background:var(--blue);flex:none}
.brand.light{color:#fff}
.brand.light .mark{background:#fff}
.contact{font-family:'Montserrat',sans-serif;font-weight:600;color:#222}
.contact p{display:flex;align-items:center;gap:3px}
.ico{flex:none;fill:var(--blue)}

/* letterhead */
.letterhead{left:242px;top:110px;width:329px;height:468px}
.letterhead .brand{position:absolute;left:29px;top:26px;font-size:11px}
.letterhead .brand .mark{width:14px;height:14px}
.letterhead .contact{position:absolute;left:224px;top:19px;border-left:1px solid var(--blue);padding-left:3px;font-size:5px;line-height:7px}
.letter{position:absolute;left:26px;top:102px;width:278px;font-size:5.6px;line-height:7.2px}
.letter .gap{margin-top:7.5px}
.letter .greet{font-weight:700;font-size:7px;margin-top:8px}
.letter .body{text-align:justify}
.letter .sign{font-family:'Parisienne',cursive;font-size:14px;margin-top:10px}

/* folder */
.folder{left:628px;top:88px;width:388px;height:490px;background:linear-gradient(90deg,var(--blue-deep),#2b66ad 60%,var(--blue-deep))}
.folder .brand{position:absolute;left:53px;top:220px;font-size:26px;gap:12px;line-height:26px}
.folder .brand .mark{width:52px;height:52px}
.folder .brand .words{display:flex;flex-direction:column}

/* email signature */
.signature{left:1042px;top:86px;width:131px;height:500px}
.signature .inner{position:absolute;left:131px;top:0;width:500px;height:131px;transform-origin:0 0;transform:rotate(90deg)}
.signature .brand{position:absolute;left:26px;top:8px;font-size:13px}
.signature .brand .mark{width:14px;height:14px}
.signature .rule{position:absolute;top:8px;width:1px;height:54px;background:var(--blue)}
.signature .who{position:absolute;left:150px;top:6px;font-family:'Montserrat',sans-serif;font-weight:600;font-size:12px;line-height:15px;color:#222}
.signature .who .name{color:var(--blue);font-weight:700}
.signature .contact{position:absolute;left:318px;top:6px;font-size:12px;line-height:15px}

/* business cards */
.card-front{left:123px;top:615px;width:151px;height:85px}
.card-front .brand{position:absolute;left:11px;top:29px;font-size:8px;gap:3px}
.card-front .brand .mark{width:9px;height:9px}
.card-front .details{position:absolute;left:85px;top:14px;border-left:1px solid var(--blue);padding-left:4px;font-family:'Montserrat',sans-serif;font-size:3.4px;line-height:5px;font-weight:600}
.card-front .details .name{color:var(--blue);font-weight:700;font-size:5px}
.card-back{left:123px;top:722px;width:151px;height:87px;background:linear-gradient(90deg,var(--blue-deep),#2b66ad)}
.card-back .brand{position:absolute;left:27px;top:36px;font-size:10px}
.card-back .brand .mark{width:13px;height:13px}

/* envelopes */
.envelope{left:312px;top:626px;width:368px;height:178px}
.envelope .brand{position:absolute;left:15px;top:20px;font-size:11px}
.envelope .brand .mark{width:13px;height:13px}
.envelope .contact{position:absolute;left:15px;top:52px;font-size:5.6px;line-height:8.4px}
.envelope-back{left:712px;top:626px;width:372px;height:178px}
.envelope-back .flap-mark{position:absolute;left:167px;top:8px;width:34px;height:34px;background:#fff}
</style>
</head>
<body>

<svg width="0" height="0" style="position:absolute">
  <defs>
    <symbol id="i-phone" viewBox="0 0 10 10"><path d="M2 1h2l1 2.5-1.3 1a6 6 0 0 0 2.8 2.8l1-1.3L10 7v2a1 1 0 0 1-1 1A9 9 0 0 1 0 1a1 1 0 0 1 1-1z"/></symbol>
    <symbol id="i-mail" viewBox="0 0 10 8"><path d="M0 0h10v8H0z M1 1l4 3 4-3" fill-rule="evenodd"/></symbol>
    <symbol id="i-web" viewBox="0 0 10 10"><circle cx="5" cy="5" r="5"/></symbol>
  </defs>
</svg>

<!-- Letterhead -->
<section class="piece letterhead">
  <div class="brand"><span class="mark"></span>STONEVALE WORKS</div>
  <div class="contact">
    <p>42-10 Harlow St 8,</p>
    <p>Ridgemont, NY 11492</p>
    <p style="margin-top:1px"><svg class="ico" width="4" height="4"><use href="#i-phone"/></svg>555-014-2290</p>
    <p><svg class="ico" width="4" height="4"><use href="#i-mail"/></svg>info@stonevaleworks.com</p>
    <p><svg class="ico" width="4" height="4"><use href="#i-web"/></svg>www.stonevaleworks.com</p>
  </div>
  <div class="letter">
    <p>Feb-03-2022</p>
    <p class="gap">Mr, Ethan Rowe<br>President</p>
    <p class="gap">Northpoint Group<br>123 Street Name, Suite# 10<br>City, State, 120023</p>
    <p class="greet">Dear Mr, Ethan</p>
    <p class="body gap">Lorem ipsum dolor sit amet, consectetur adipisicing elit, sed do eiusmod tempor incididunt ut labore et dolore magna aliqua. Ut enim ad minim veniam, quis nostrud exercitation ullamco laboris nisi ut aliquip ex ea commodo consequat. Duis aute irure dolor in reprehenderit in voluptate velit esse cillum dolore eu fugiat nulla pariatur.</p>
    <p class="body gap">Lorem ipsum dolor sit amet, consectetur adipisicing elit, sed do eiusmod tempor incididunt ut labore et dolore magna aliqua. Ut enim ad minim veniam, quis nostrud exercitation ullamco laboris nisi ut aliquip ex ea commodo consequat. Duis aute irure dolor in reprehenderit in voluptate velit esse cillum dolore eu fugiat nulla pariatur.</p>
    <p class="body gap">Lorem ipsum dolor sit amet, consectetur adipisicing elit, sed do eiusmod tempor incididunt ut labore et dolore magna aliqua. Ut enim ad minim veniam, quis nostrud exercitation ullamco laboris nisi ut aliquip ex ea commodo consequat.</p>
    <p class="body gap">Excepteur sint occaecat cupidatat non proident, sunt in culpa qui officia deserunt mollit anim id est laborum. re et dolore magnam aliquam quaerat voluptatem.</p>
    <p style="margin-top:14px">Regards</p>
    <p class="sign">Daniel Hart</p>
  </div>
  <svg class="band" width="329" height="70" viewBox="0 0 329 70">
    <path d="M0 12 Q164 72 329 0 V70 H0Z" fill="var(--blue)"/>
    <path d="M15 3 Q164 60 308 6 Q164 52 15 3Z" fill="var(--curve)"/>
  </svg>
</section>

<!-- Folder -->
<section class="piece folder">
  <div class="brand light"><span class="mark"></span><span class="words"><span>STONEVALE</span><span>WORKS</span></span></div>
</section>

<!-- Email signature -->
<section class="piece signature">
  <div class="inner">
    <div class="brand"><span class="mark"></span>STONEVALE</div>
    <div class="rule" style="left:140px"></div>
    <div class="who">
      <p class="name">ALDEN MARROWAY</p>
      <p>Managing Director</p>
      <p>Suite 4B Larchfield IL 60</p>
    </div>
    <div class="rule" style="left:306px"></div>
    <div class="contact">
      <p><svg class="ico" width="9" height="9"><use href="#i-phone"/></svg>555-017-3344</p>
      <p><svg class="ico" width="9" height="8"><use href="#i-mail"/></svg>info@yourmail.com</p>
      <p><svg class="ico" width="9" height="9"><use href="#i-web"/></svg>www.yourwebsite.com</p>
    </div>
    <svg class="band" width="500" height="62" viewBox="0 0 500 62">
      <path d="M0 14 Q250 70 500 14 V62 H0Z" fill="var(--blue)"/>
      <path d="M18 0 Q250 64 482 0 Q250 54 18 0Z" fill="var(--curve)"/>
    </svg>
  </div>
</section>

<!-- Business card front -->
<section class="piece card-front">
  <div class="brand"><span class="mark"></span>STONEVALE</div>
  <div class="details">
    <p class="name">CARL PENWICK</p>
    <p>Co-Founder</p>
    <p style="margin-top:2px">42-10 Harlow St 8,<br>Ridgemont, NY 11492</p>
    <p>555-014-2290</p>
    <p>info@stonevaleworks.com</p>
    <p>www.stonevaleworks.com</p>
  </div>
  <svg class="band" width="151" height="24" viewBox="0 0 151 24">
    <path d="M0 6 Q75 26 151 0 V24 H0Z" fill="var(--blue)"/>
    <path d="M14 3 Q75 20 140 3 Q75 16 14 3Z" fill="var(--curve)"/>
  </svg>
</section>

<!-- Business card back -->
<section class="piece card-back">
  <div class="brand light"><span class="mark"></span>STONEVALE</div>
</section>

<!-- Envelope front -->
<section class="piece envelope">
  <div class="brand"><span class="mark"></span>STONEVALE WORKS</div>
  <div class="contact">
    <p>42-10 Harlow St 8,</p>
    <p>Ridgemont, NY 11492</p>
    <p style="margin-top:3px"><svg class="ico" width="5" height="5"><use href="#i-phone"/></svg>555-014-2290</p>
    <p><svg class="ico" width="5" height="4"><use href="#i-mail"/></svg>info@stonevaleworks.com</p>
    <p><svg class="ico" width="5" height="5"><use href="#i-web"/></svg>www.stonevaleworks.com</p>
  </div>
  <svg class="band" width="368" height="62" viewBox="0 0 368 62">
    <path d="M0 0 Q184 70 368 0 V62 H0Z" fill="var(--blue)"/>
    <path d="M16 4 Q184 55 340 10 Q184 46 16 4Z" fill="var(--curve)"/>
  </svg>
</section>

<!-- Envelope back -->
<section class="piece envelope-back">
  <svg width="372" height="54" viewBox="0 0 372 54" style="position:absolute;left:0;top:0">
    <path d="M0 0 H372 L355 40 Q350 53 336 53 H36 Q22 53 17 40Z" fill="var(--blue)"/>
  </svg>
  <span class="flap-mark"></span>
</section>

</body>
</html>
```